Company director needs a business card design

I am a semi-retired former senior finance executive who sits on a number of public and private company boards and do some consulting work. I work largely with emerging businesses but deal regularly with top end of town lawyers, bankers etc. I need a thoughtful but relatively conservative design which would also resonate with my younger client base. Some colour would be good. Information limited to name, address, office tel, mobile and email.

Finance

```html
<!DOCTYPE html>
<html lang="en">
<head>
<meta charset="utf-8">
<title>Business Card – Morgan</title>
<link href="https://fonts.googleapis.com/css2?family=Open+Sans:wght@400;700&display=swap" rel="stylesheet">
<style>
  :root {
    --backdrop: #e9ebef;
    --card-blue: #1d55a5;
    --ornament-light: #4a7fc6;
    --ink-white: #ffffff;
    --accent-orange: #f0a13a;
  }
  html, body {
    margin: 0;
    width: 1200px;
    height: 800px;
    overflow: hidden;
    background: var(--backdrop);
    font-family: "Open Sans", Arial, sans-serif;
  }
  .card {
    position: absolute;
    left: 100px;
    top: 114px;
    width: 1000px;
    height: 572px;
    background: var(--card-blue);
    overflow: hidden;
    box-shadow: 0 10px 30px rgba(0,0,0,0.18);
  }
  .brush-ring-area {
    position: absolute;
    left: 20px;
    top: 60px;
    width: 480px;
    height: 512px;
    background: radial-gradient(ellipse at center, var(--ornament-light) 0%, var(--card-blue) 72%);
  }
  .rule {
    position: absolute;
    height: 5px;
    background: var(--ink-white);
  }
  .rule-top { left: 520px; top: 128px; width: 360px; }
  .rule-middle { left: 556px; top: 242px; width: 204px; }
  .identity {
    position: absolute;
    left: 200px;
    top: 300px;
    line-height: 1.1;
  }
  .identity .name {
    margin: 0;
    font-weight: 700;
    font-size: 32px;
    color: var(--ink-white);
  }
  .identity .role {
    margin: 0 0 0 22px;
    font-weight: 400;
    font-size: 21px;
    color: var(--accent-orange);
  }
  .contact-list {
    position: absolute;
    left: 526px;
    top: 150px;
    margin: 0;
    padding: 0;
    list-style: none;
  }
  .contact-list li {
    display: flex;
    align-items: center;
    height: 40px;
    font-size: 20px;
    color: var(--accent-orange);
  }
  .contact-list li.after-rule { margin-top: 24px; }
  .contact-list svg {
    width: 20px;
    height: 20px;
    margin-right: 22px;
    fill: var(--ink-white);
  }
</style>
</head>
<body>
  <div class="card">
    <div class="brush-ring-area" role="img" aria-label="Large white hand-painted brush-stroke ring framing the name"></div>

    <div class="rule rule-top"></div>
    <div class="rule rule-middle"></div>

    <div class="identity">
      <p class="name">Morgan</p>
      <p class="role">manager</p>
    </div>

    <ul class="contact-list">
      <li>
        <svg viewBox="0 0 24 24"><path d="M6.6 10.8a15 15 0 0 0 6.6 6.6l2.2-2.2c.3-.3.7-.4 1-.2 1.1.4 2.3.6 3.6.6.6 0 1 .4 1 1V20c0 .6-.4 1-1 1A17 17 0 0 1 3 4c0-.6.4-1 1-1h3.5c.6 0 1 .4 1 1 0 1.3.2 2.5.6 3.6.1.3 0 .7-.2 1z"/></svg>
        5550-1274
      </li>
      <li>
        <svg viewBox="0 0 24 24"><path d="M7 1h10a2 2 0 0 1 2 2v18a2 2 0 0 1-2 2H7a2 2 0 0 1-2-2V3a2 2 0 0 1 2-2zm0 3v14h10V4zm5 15.5a1 1 0 1 0 0 2 1 1 0 0 0 0-2z"/></svg>
        00 555 018 342
      </li>
      <li class="after-rule">
        <svg viewBox="0 0 24 24"><path d="M12 2a7 7 0 0 0-7 7c0 5 7 13 7 13s7-8 7-13a7 7 0 0 0-7-7zm0 9.5a2.5 2.5 0 1 1 0-5 2.5 2.5 0 0 1 0 5z"/></svg>
        42 Harbour Lane, BC
      </li>
      <li>
        <svg viewBox="0 0 24 24"><path d="M2 5h20v14H2zm2 2v.5l8 5 8-5V7zm0 2.8V17h16V9.8l-8 5z"/></svg>
        email-morgan42@mailbox.com
      </li>
    </ul>
  </div>
</body>
</html>
```